Company Website Re-design for Software development consultancy

We would like our company website to be redesigned using our existing marketing collateral and website content as a guide

current site : www.brightkestrel.com.au

For the different pages types and content please base on the following site : https://www.quorvalabs.net/

We want a coded site - but will replace the content ourselves within the sections you provide to customise to our needs.

Target Market(s)

Medium to Large corporates needing software design and development services

Industry/Entity Type

Information Technology

Coding

Coded - Design and coding required

Number of Pages Required

5+ page

Font styles to use
Sans Serif

Colors
ec1f27
ffffff
000000

Requirements
Must have
• Align to colour scheme of existing collateral
• Include pages for the key areas of our busines - see : https://www.quorvalabs.net/
Nice to have
• image rotators - make the site interesting to the business visitor

```html
<!DOCTYPE html>
<html lang="en">
<head>
<meta charset="utf-8">
<title>Bright Kestrel — Software Development Consultancy</title>
<link href="https://fonts.googleapis.com/css2?family=Roboto:wght@300;400;500;700&family=Roboto+Condensed:wght@300;400;700&display=swap" rel="stylesheet">
<style>
:root{
  --red:#ec1f27;
  --white:#ffffff;
  --black:#000000;
  --ink:#1c1c1c;
  --text:#555555;
  --muted:#8a8a8a;
  --panel:#f2f2f2;
  --dark:#222222;
  --darker:#151515;
  --line:#dddddd;
}
*{box-sizing:border-box;margin:0;padding:0}
html,body{width:1200px;height:3448px;overflow:hidden}
body{position:relative;background:var(--white);font-family:"Roboto",Arial,sans-serif;color:var(--text)}
.abs{position:absolute}

/* hero */
.hero{left:0;top:0;width:1200px;height:591px;background:linear-gradient(160deg,#4a4d52 0%,#2b2e33 45%,#5d6168 70%,#23262a 100%)}
.brand{left:172px;top:20px;font-family:"Roboto Condensed",sans-serif;font-weight:700;font-size:30px;color:var(--white);letter-spacing:1px}
.nav{right:170px;top:36px;display:flex;gap:24px}
.nav a{color:var(--white);text-decoration:none;font-size:12px;font-weight:500;letter-spacing:.3px}

/* three faces */
.faces-title{left:0;width:1200px;top:630px;text-align:center;font-family:"Roboto Condensed",sans-serif;font-weight:700;font-size:33px;color:var(--ink)}
.faces-sub{left:450px;width:300px;top:680px;height:26px;line-height:26px;background:var(--panel);text-align:center;font-size:11px;color:var(--muted);letter-spacing:.3px;white-space:nowrap}
.card{top:736px;width:270px;height:334px;background:var(--panel)}
.card .photo{height:192px;background:linear-gradient(135deg,#b9bcc1,#6f747b)}
.card h3{margin-top:16px;text-align:center;font-size:15px;font-weight:700;color:var(--ink);letter-spacing:.4px}
.card p{margin:8px 18px 0;text-align:center;font-size:11.5px;line-height:18px;color:var(--text);height:44px}
.card .btn{position:absolute;left:0;bottom:0;width:100%;height:40px;line-height:40px;background:var(--red);color:var(--white);text-align:center;font-size:12px;font-weight:700}

/* welcome */
.welcome-left{left:0;top:1122px;width:605px;height:474px;background:linear-gradient(120deg,#d9dde2,#8f97a1 55%,#3e4a5a)}
.welcome-panel{left:605px;top:1122px;width:297px;height:474px;background:var(--panel);padding:28px 32px}
.welcome-right{left:902px;top:1122px;width:298px;height:474px;background:linear-gradient(140deg,#e6e7ea,#b8b3ae 50%,#3b3431)}
.welcome-panel .kicker{font-family:"Roboto Condensed",sans-serif;font-weight:300;font-size:27px;color:var(--ink);line-height:30px}
.welcome-panel h2{font-family:"Roboto Condensed",sans-serif;font-weight:700;font-size:30px;color:var(--ink);line-height:34px}
.welcome-panel p{margin-top:12px;font-size:10px;line-height:16px;color:var(--text)}
.welcome-panel .btn{display:inline-block;margin-top:14px;background:var(--red);color:var(--white);font-size:11px;font-weight:700;padding:9px 20px}

/* services */
.svc-kicker{left:0;width:1200px;top:1640px;text-align:center;font-size:12px;color:var(--muted);letter-spacing:.6px}
.svc-title{left:0;width:1200px;top:1664px;text-align:center;font-family:"Roboto Condensed",sans-serif;font-weight:700;font-size:38px;color:var(--red);line-height:44px}
.svc-sub{left:0;width:1200px;top:1706px;text-align:center;font-family:"Roboto Condensed",sans-serif;font-weight:700;font-size:25px;color:var(--ink)}
.svc{width:280px;height:90px}
.svc svg{position:absolute;left:0;top:2px}
.svc h4{margin-left:52px;font-size:11.5px;font-weight:700;color:var(--ink);letter-spacing:.2px}
.svc p{margin-left:52px;margin-top:8px;font-size:11px;line-height:16.5px;color:var(--text)}

/* tell us */
.tell{left:0;top:2024px;width:589px;height:414px;background:var(--red)}
.tell h2{position:absolute;left:172px;top:24px;font-family:"Roboto Condensed",sans-serif;font-weight:700;font-size:54px;color:var(--white);line-height:56px}
.tell .tag{position:absolute;left:174px;top:80px;font-size:16px;letter-spacing:6px;color:var(--white)}
.field{position:absolute;height:32px;background:var(--white);font-size:10px;color:var(--muted);padding:0 10px;line-height:32px}
.tell .submit{position:absolute;left:172px;top:334px;width:373px;height:44px;background:var(--darker);color:var(--white);font-family:"Roboto Condensed",sans-serif;font-weight:700;font-size:20px;text-align:center;line-height:44px}
.stats{left:589px;top:2024px;width:611px;height:414px;background:linear-gradient(135deg,#2c2c2c,#1a1a1a)}
.stat{position:absolute;width:200px;text-align:center;color:var(--white)}
.stat svg{display:block;margin:0 auto}
.stat b{display:block;margin-top:8px;font-size:36px;font-weight:500;line-height:40px}
.stat span{display:block;margin-top:2px;font-size:16px;color:#cfcfcf}

/* leadership */
.lead-title{left:0;width:1200px;top:2482px;text-align:center;font-family:"Roboto Condensed",sans-serif;font-weight:700;font-size:27px;color:var(--ink)}
.lead-rule{left:540px;top:2524px}
.lead-intro{left:240px;width:720px;top:2548px;text-align:center;font-size:11.5px;line-height:20px;color:var(--text)}
.member{top:2640px;width:243px;height:332px;background:linear-gradient(160deg,#c7cbd1,#5b6470)}
.member .soc{position:absolute;right:0;top:0;width:34px;height:118px;background:var(--red);display:flex;flex-direction:column;align-items:center;justify-content:space-around;padding:6px 0}
.member .soc i{display:block;width:8px;height:8px;border-radius:50%;background:var(--white)}
.member .name{position:absolute;left:12px;bottom:20px;background:var(--darker);color:var(--white);padding:6px 12px;min-width:110px}
.member .name b{display:block;font-size:10.5px;font-weight:700}
.member .name span{display:block;font-size:9px;color:#cfcfcf;margin-top:2px}

/* newsletter */
.news{left:0;top:3054px;width:1200px;height:81px;background:var(--red)}
.news h3{position:absolute;left:160px;top:29px;font-family:"Roboto Condensed",sans-serif;font-weight:700;font-size:17px;color:var(--white)}
.news .input{position:absolute;left:408px;top:27px;width:337px;height:28px;background:var(--white);font-size:10px;color:var(--muted);padding:0 10px;line-height:28px}
.news .go{position:absolute;left:745px;top:27px;width:80px;height:28px;background:var(--darker);color:var(--white);font-size:11px;line-height:28px;text-align:center}
.news .socials{position:absolute;left:866px;top:26px;display:flex;gap:20px}
.news .socials i{display:flex;align-items:center;justify-content:center;width:30px;height:30px;background:var(--white)}
.news .socials i::after{content:"";width:10px;height:10px;border-radius:50%;background:var(--darker)}

/* footer */
.footer{left:0;top:3135px;width:1200px;height:265px;background:var(--dark)}
.fcol{position:absolute;top:40px;color:var(--white)}
.fcol h4{font-size:15px;font-weight:500;margin-bottom:16px}
.fcol li{list-style:none;font-size:10px;color:#bdbdbd;line-height:23px;padding-left:12px;position:relative}
.fcol li::before{content:"";position:absolute;left:0;top:10px;width:4px;height:4px;background:#bdbdbd;border-radius:50%}
.quote{position:absolute;left:0;top:38px;width:248px;height:98px;border:1px solid #4a4a4a;padding:14px 14px 0 38px;font-size:10px;font-style:italic;line-height:16px;color:#bdbdbd}
.quote svg{position:absolute;left:12px;top:14px}
.quote-author{position:absolute;top:146px;left:4px;font-size:10px;color:#9a9a9a}
.loc{display:flex;align-items:center;gap:10px;font-size:10.5px;color:#d0d0d0;margin-bottom:18px;white-space:nowrap}
.loc.big{font-size:14px;color:var(--white)}
.bottom{left:0;top:3400px;width:1200px;height:48px;background:var(--darker)}
.bottom p{position:absolute;left:160px;top:18px;font-size:9.5px;color:#aaaaaa}
.bottom .socials{position:absolute;left:912px;top:13px;display:flex;gap:12px}
.bottom .socials i{display:flex;align-items:center;justify-content:center;width:22px;height:22px;border:1px solid #8a8a8a;border-radius:50%}
.bottom .socials i::after{content:"";width:6px;height:6px;border-radius:50%;background:#aaaaaa}
</style>
</head>
<body>

<!-- hero -->
<div class="abs hero" role="img" aria-label="Photo of a software team working at laptops in an open-plan office"></div>
<div class="abs brand">BRIGHT KESTREL</div>
<nav class="abs nav"><a>HOME</a><a>ABOUT US</a><a>OUR SERVICES</a><a>PROJECT</a><a>CONTACT US</a></nav>

<!-- three faces -->
<h2 class="abs faces-title">THE THREE FACES OF BRIGHT KESTREL</h2>
<div class="abs faces-sub">WE ARE ALL ABOUT BUILDING SOFTWARE BETTER.</div>

<div class="abs card" style="left:172px">
  <div class="photo" role="img" aria-label="Photo of a consultant smiling at her laptop"></div>
  <h3>CONSULTING</h3>
  <p>Up-skill your team by using our consultants- for either short or long term engagements.</p>
  <div class="btn">VIEW MORE INFO</div>
</div>
<div class="abs card" style="left:465px">
  <div class="photo" role="img" aria-label="Photo of hands working over project plans on a desk"></div>
  <h3>PROJECTS</h3>
  <p>We can deliver a large project on a fixed price basis at a quality standard you won't believe</p>
  <div class="btn">VIEW MORE INFO</div>
</div>
<div class="abs card" style="left:758px">
  <div class="photo" role="img" aria-label="Photo of a team meeting around a table with laptops"></div>
  <h3>FASTTRACK</h3>
  <p>Our product, FastTrack, allows you to skip the development cycle and turn</p>
  <div class="btn">VIEW MORE INFO</div>
</div>

<!-- welcome -->
<div class="abs welcome-left" role="img" aria-label="Photo of a smiling business team holding a laptop"></div>
<div class="abs welcome-panel">
  <div class="kicker">WELCOME TO</div>
  <h2>BRIGHT KESTREL</h2>
  <p>Lorem Ipsum is simply dummy text of the printing and typesetting industry. Lorem Ipsum has been the industry's standard dummy text ever since the 1500s, when an unknown printer took a galley of type and scrambled it to make a type specimen book. It has survived not only five centuries, but also the leap into electronic typesetting, remaining essentially unchanged. It was popularised in the containing Lorem Ipsum passages, and more recently with desktop publishing software like Aldus PageMaker including versions of Lorem Ipsum.</p>
  <p>Lorem Ipsum is simply dummy text of the printing and typesetting industry. Lorem Ipsum has been the industry's standard dummy text ever since the type recently with desktop publishing software like Aldus PageMaker including versions of Lorem Ipsum.</p>
  <span class="btn">MORE INFO</span>
</div>
<div class="abs welcome-right" role="img" aria-label="Photo of a woman working on a laptop"></div>

<!-- services -->
<div class="abs svc-kicker">OUR SERVICES</div>
<h2 class="abs svc-title">WE PROVIDE WIDE RANGE</h2>
<div class="abs svc-sub">OF SOFTWARE SERVICES</div>

<div class="abs svc" style="left:172px;top:1782px">
  <svg width="36" height="36" viewBox="0 0 36 36" fill="none" stroke="#ec1f27" stroke-width="2"><rect x="3" y="5" width="30" height="20" rx="2"/><path d="M13 31h10M18 25v6"/></svg>
  <h4>ENTERPRISE SOFTWARE DEVELOPMENT</h4>
  <p>Lorem Ipsum is simply dummy text printing and typesetting industry. Lorem Ipsum has been the industry's standard dummy text</p>
</div>
<div class="abs svc" style="left:472px;top:1782px">
  <svg width="36" height="36" viewBox="0 0 36 36" fill="none" stroke="#ec1f27" stroke-width="2"><rect x="9" y="3" width="18" height="30" rx="3"/><path d="M15 28h6"/></svg>
  <h4>MOBILE APP DEVELOPMENT</h4>
  <p>Lorem Ipsum is simply dummy text printing and typesetting industry. Lorem Ipsum has been the industry's standard dummy text</p>
</div>
<div class="abs svc" style="left:752px;top:1782px">
  <svg width="36" height="36" viewBox="0 0 36 36" fill="none" stroke="#ec1f27" stroke-width="2"><circle cx="18" cy="18" r="6"/><circle cx="18" cy="18" r="13" stroke-dasharray="5 4"/></svg>
  <h4>IT CONSULTING</h4>
  <p>Lorem Ipsum is simply dummy text printing and typesetting industry. Lorem Ipsum has been the industry's standard dummy text</p>
</div>
<div class="abs svc" style="left:172px;top:1897px">
  <svg width="36" height="36" viewBox="0 0 36 36" fill="#ec1f27"><circle cx="18" cy="9" r="5"/><path d="M10 30v-8a8 8 0 0 1 16 0v8z"/><circle cx="6" cy="14" r="3.5"/><circle cx="30" cy="14" r="3.5"/><path d="M1 30v-5a5 5 0 0 1 8-4v9zM35 30v-5a5 5 0 0 0-8-4v9z"/></svg>
  <h4>DEDICATED DEVELOPMENT TEAM</h4>
  <p>Lorem Ipsum is simply dummy text printing and typesetting industry. Lorem Ipsum has been the industry's standard dummy text</p>
</div>
<div class="abs svc" style="left:472px;top:1897px">
  <svg width="36" height="36" viewBox="0 0 36 36" fill="none" stroke="#ec1f27" stroke-width="2"><rect x="3" y="8" width="24" height="18" rx="2"/><rect x="20" y="14" width="13" height="17" rx="2" fill="#fff"/><path d="M8 31h12"/></svg>
  <h4>UI AND UX DESIGN SERVICES</h4>
  <p>Lorem Ipsum is simply dummy text printing and typesetting industry. Lorem Ipsum has been the industry's standard dummy text</p>
</div>
<div class="abs svc" style="left:752px;top:1897px">
  <svg width="36" height="36" viewBox="0 0 36 36" fill="none" stroke="#ec1f27" stroke-width="2"><rect x="5" y="4" width="20" height="26" rx="2"/><path d="M10 11h10M10 16h10M10 21h6"/><circle cx="26" cy="26" r="7" fill="#fff"/><path d="M23 26l2 2 4-4"/></svg>
  <h4>QA AND SOFTWARE TESTING</h4>
  <p>Lorem Ipsum is simply dummy text printing and typesetting industry. Lorem Ipsum has been the industry's standard dummy text</p>
</div>

<!-- tell us -->
<section class="abs tell">
  <h2>TELL US</h2>
  <div class="tag">ABOUT YOUR PROJECT</div>
  <div class="field" style="left:172px;top:112px;width:182px">I am interested in</div>
  <div class="field" style="left:366px;top:112px;width:179px">Email</div>
  <div class="field" style="left:172px;top:152px;width:182px">Work Phone</div>
  <div class="field" style="left:366px;top:152px;width:179px">Company</div>
  <div class="field" style="left:172px;top:192px;width:182px">Country</div>
  <div class="field" style="left:366px;top:192px;width:179px">Name</div>
  <div class="field" style="left:172px;top:232px;width:373px;height:88px">Project Description</div>
  <div class="submit">TALK TO OUR TEAM</div>
</section>
<section class="abs stats">
  <div class="stat" style="left:29px;top:50px">
    <svg width="44" height="48" viewBox="0 0 44 48" fill="none" stroke="#fff" stroke-width="2"><rect x="8" y="4" width="28" height="40" rx="2"/><path d="M14 14h16M14 21h16M14 28h16M14 35h10"/></svg>
    <b>62000+</b><span>Projects</span>
  </div>
  <div class="stat" style="left:259px;top:50px">
    <svg width="44" height="48" viewBox="0 0 44 48" fill="none" stroke="#fff" stroke-width="2"><circle cx="22" cy="14" r="9"/><path d="M6 44v-6a16 16 0 0 1 32 0v6z"/></svg>
    <b>246000</b><span>Happy Clients</span>
  </div>
  <div class="stat" style="left:29px;top:246px">
    <svg width="48" height="48" viewBox="0 0 48 48" fill="none" stroke="#fff" stroke-width="2"><circle cx="24" cy="24" r="20"/><path d="M24 12v12l8 6"/></svg>
    <b>1200</b><span>Hours of Work</span>
  </div>
  <div class="stat" style="left:259px;top:246px">
    <svg width="48" height="48" viewBox="0 0 48 48" fill="none" stroke="#fff" stroke-width="2"><rect x="6" y="6" width="16" height="16"/><rect x="26" y="6" width="16" height="16"/><rect x="6" y="26" width="16" height="16"/><rect x="26" y="26" width="16" height="16"/></svg>
    <b>12000</b><span>Solutions</span>
  </div>
</section>

<!-- leadership -->
<h2 class="abs lead-title">MEET OUR LEADERSHIP TEAM</h2>
<svg class="abs lead-rule" width="120" height="14" viewBox="0 0 120 14"><path d="M0 7h38M82 7h38" stroke="#999" stroke-width="1"/><circle cx="46" cy="7" r="2.5" fill="#1c1c1c"/><path d="M60 0l2 5h5l-4 3 1.6 5L60 10l-4.6 3L57 8l-4-3h5z" fill="#ec1f27"/><circle cx="74" cy="7" r="2.5" fill="#1c1c1c"/></svg>
<p class="abs lead-intro">Between just the partners, we have more than 60 years of software development experience. We combine a solid knowledge of computer science with a practical, pragmatic approach to delivering software.</p>

<div class="abs member" style="left:172px" role="img" aria-label="Portrait photo of a leadership team member in a suit">
  <div class="soc"><i></i><i></i><i></i></div>
  <div class="name"><b>DANIEL ORMOND</b><span>Lorem ipsum is simply</span></div>
</div>
<div class="abs member" style="left:483px" role="img" aria-label="Portrait photo of a leadership team member in a blazer">
  <div class="soc"><i></i><i></i><i></i></div>
  <div class="name"><b>CLARA WENSLEY</b><span>Lorem ipsum is simply</span></div>
</div>
<div class="abs member" style="left:786px" role="img" aria-label="Portrait photo of a leadership team member in a suit and tie">
  <div class="soc"><i></i><i></i><i></i></div>
  <div class="name"><b>MARTIN CALLOWAY</b><span>Lorem ipsum is simply</span></div>
</div>

<!-- newsletter -->
<section class="abs news">
  <h3>SIGN UP FOR NEWSLETTER</h3>
  <div class="input">Your email address</div>
  <div class="go">Subscribe</div>
  <div class="socials"><i></i><i></i><i></i><i></i></div>
</section>

<!-- footer -->
<footer class="abs footer">
  <div class="fcol" style="left:158px">
    <h4>Quick Links</h4>
    <ul><li>Home</li><li>About Us</li><li>Our Services</li><li>Project</li><li>Blog</li><li>Contact Us</li></ul>
  </div>
  <div class="fcol" style="left:320px">
    <h4>Our Services</h4>
    <ul><li>Mobile Development</li><li>IT Consulting</li><li>App Developers</li><li>Android App Development</li><li>Windows App Development</li><li>Cloud Services</li></ul>
  </div>
  <div class="fcol" style="left:525px;width:250px">
    <h4>Testimonials</h4>
    <div class="quote">
      <svg width="18" height="14" viewBox="0 0 18 14" fill="#8a8a8a"><path d="M0 14V8C0 3 3 0 7 0v3C5 3 4 5 4 7h3v7zM11 14V8c0-5 3-8 7-8v3c-2 0-3 2-3 4h3v7z"/></svg>
      Lorem Ipsum is simply dummy text of the Ipsum has been the industry's standard dummy text ever since unknown the leap into electronic typesetting
    </div>
    <div class="quote-author">Ian Hollister</div>
  </div>
  <div class="fcol" style="left:843px;width:220px">
    <h4>Get in Location</h4>
    <div class="loc"><svg width="12" height="16" viewBox="0 0 12 16" fill="#d0d0d0"><path d="M6 0a6 6 0 0 1 6 6c0 4-6 10-6 10S0 10 0 6a6 6 0 0 1 6-6zm0 3a3 3 0 1 0 0 6 3 3 0 0 0 0-6z"/></svg>42 - 44 Harbour Ln, Sydney 2000</div>
    <div class="loc"><svg width="14" height="10" viewBox="0 0 14 10" fill="none" stroke="#d0d0d0"><rect x=".5" y=".5" width="13" height="9"/><path d="M.5.5L7 6l6.5-5.5"/></svg>info@brightkestrel.com.au</div>
    <div class="loc big"><svg width="14" height="14" viewBox="0 0 14 14" fill="#d0d0d0"><path d="M3 0l3 3-2 2a8 8 0 0 0 5 5l2-2 3 3-2 3C6 14 0 8 0 2z"/></svg>555-014-2290</div>
    <div class="loc big"><svg width="14" height="14" viewBox="0 0 14 14" fill="#d0d0d0"><path d="M3 0l3 3-2 2a8 8 0 0 0 5 5l2-2 3 3-2 3C6 14 0 8 0 2z"/></svg>555-014-2290</div>
  </div>
</footer>
<div class="abs bottom">
  <p>© 2018 www.brightkestrel.com.au. All Right Reserved</p>
  <div class="socials"><i></i><i></i><i></i><i></i></div>
</div>

</body>
</html>
```